Harborview Estates Business Card for Apartment Buildings

Create business cards for resident managers who run apartment buildings. The audience is the public who are searching for apartment rentals, and current residents who live at the apartment building. Key design element will be incorporating the company logo, however, the logo cannot dominate. The building name and manager name are more important than the logo. Current business card design leaves little room for copy, so we may need to reduce the size on the current card to allow for more space for copy.

Target Market(s)

Adults 18-65 years of age, who are looking for an apartment rental, plus current residents who live at our apartment buildings.

Industry/Entity Type

Property Management

Contact Information for Business Card

A major design element will be use of the company logo. Important property and manager contact information must be part of the design. The size of the logo will need to be reduced to make room for building and manager contact copy.

Font styles to use
Sans Serif

Colors
3176b5
000000
959595
ffffff

Requirements
Must have
• 1) Incorporate the company logo.
• 2) Use the company colors (dark blue, black/grey, over white).
• 3) FEATURE THE BUILDING NAME
• 4) FEATURE THE MANAGER NAME
• 5) The company name is less important than BUILDING and MANAGER
• 6) Manager contact information
• **SEE ATTACHED CREATIVE BRIEF**
Nice to have
• 1) Back of card logo watermark
• 2) Ability to write notes on back of carfd
Should not have
• Avoid letting the company logo dominate the card, the building name and manager are more important than the company logo.

```html
<!DOCTYPE html>
<html lang="en">
<head>
<meta charset="utf-8">
<title>Harborview Estates Business Card</title>
<link rel="stylesheet" href="https://fonts.googleapis.com/css2?family=Roboto:wght@400;500;700&family=Roboto+Condensed:wght@700&display=swap">
<style>
  :root {
    --brand-blue: #1767a8;
    --ink-dark: #3d4247;
    --ink-text: #444444;
    --card-white: #f3f3f3;
    --backdrop: #262626;
    --watermark: #e3e3e3;
  }
  * { margin: 0; padding: 0; box-sizing: border-box; }
  html, body { width: 1200px; height: 960px; overflow: hidden; }
  body {
    background: var(--backdrop);
    font-family: "Roboto", sans-serif;
    position: relative;
  }
  .card {
    position: absolute;
    width: 600px;
    height: 342px;
    background: var(--card-white);
    box-shadow: 0 3px 8px rgba(0,0,0,.55);
    overflow: hidden;
  }
  .card-front { left: 314px; top: 113px; }
  .card-back  { left: 311px; top: 472px; height: 343px; }

  .company-mark {
    position: absolute;
    right: 41px;
    top: 64px;
    display: flex;
    align-items: center;
    gap: 8px;
    font-family: "Roboto Condensed", sans-serif;
    font-weight: 700;
    font-size: 25px;
    color: var(--brand-blue);
    text-transform: uppercase;
  }
  .company-mark .mark-square {
    width: 18px; height: 18px; background: var(--brand-blue);
  }

  .property { position: absolute; left: 41px; top: 142px; }
  .property-name {
    font-family: "Roboto Condensed", sans-serif;
    font-weight: 700;
    font-size: 22px;
    color: var(--brand-blue);
    line-height: 26px;
  }
  .property-address {
    font-size: 14.5px;
    color: var(--ink-text);
    line-height: 19px;
  }

  .contact-list {
    position: absolute; left: 42px; top: 212px;
    list-style: none;
    font-size: 14.5px;
    color: var(--ink-text);
  }
  .contact-list li {
    display: flex; align-items: center; gap: 8px; height: 19px;
  }
  .contact-list svg { width: 14px; height: 14px; fill: var(--brand-blue); }

  .manager {
    position: absolute; right: 41px; top: 240px; text-align: right;
  }
  .manager-name {
    font-family: "Roboto Condensed", sans-serif;
    font-weight: 700;
    font-size: 22.5px;
    color: var(--brand-blue);
    line-height: 28px;
  }
  .manager-title {
    font-weight: 500;
    font-size: 15px;
    color: var(--ink-dark);
  }

  .footer-bands { position: absolute; left: 0; bottom: 0; width: 600px; height: 36px; }
  .web-address {
    position: absolute; right: 37px; bottom: 10px;
    font-size: 14px; letter-spacing: 1.6px; color: #ffffff;
  }

  .back-watermark {
    position: absolute; inset: 0;
    display: flex; align-items: center; justify-content: center;
    font-family: "Roboto Condensed", sans-serif;
    font-weight: 700;
    font-size: 56px;
    color: var(--watermark);
    text-transform: uppercase;
  }
</style>
</head>
<body>

<section class="card card-front">
  <div class="company-mark"><span class="mark-square"></span>Harborview Estates</div>

  <div class="property">
    <h1 class="property-name">Bayside Court Apartments</h1>
    <p class="property-address">2480 Linden Avenue<br>Riverton, CA 90210</p>
  </div>

  <ul class="contact-list">
    <li><svg viewBox="0 0 24 24"><path d="M6.6 10.8a15 15 0 0 0 6.6 6.6l2.2-2.2c.3-.3.7-.4 1-.2 1.1.4 2.3.6 3.6.6.6 0 1 .4 1 1V20c0 .6-.4 1-1 1C10.6 21 3 13.4 3 4c0-.6.4-1 1-1h3.5c.6 0 1 .4 1 1 0 1.3.2 2.5.6 3.6.1.3 0 .7-.2 1z"/></svg>555-210-4830</li>
    <li><svg viewBox="0 0 24 24"><path d="M7 1h10a2 2 0 0 1 2 2v18a2 2 0 0 1-2 2H7a2 2 0 0 1-2-2V3a2 2 0 0 1 2-2zm0 3v15h10V4zm5 16.2a1 1 0 1 0 0 .1z"/></svg>555-374-9152</li>
    <li><svg viewBox="0 0 24 24"><path d="M7 2h10v5H7zM4 8h16a2 2 0 0 1 2 2v7h-4v5H6v-5H2v-7a2 2 0 0 1 2-2zm4 8v4h8v-4z"/></svg>555-608-2417</li>
    <li><svg viewBox="0 0 24 24"><path d="M2 5h20v14H2zm2 2v.5l8 5 8-5V7zm0 2.8V17h16V9.8l-8 5z"/></svg>marisol@harborviewest.com</li>
  </ul>

  <div class="manager">
    <h2 class="manager-name">Marisol Vega</h2>
    <p class="manager-title">Resident Manager</p>
  </div>

  <svg class="footer-bands" viewBox="0 0 600 36" aria-hidden="true">
    <rect x="0" y="13" width="346" height="10" fill="var(--ink-dark)"/>
    <rect x="0" y="26" width="600" height="10" fill="var(--brand-blue)"/>
    <polygon points="336,36 358,0 600,0 600,36" fill="#ffffff"/>
    <polygon points="340,36 361,2 600,2 600,36" fill="var(--brand-blue)"/>
  </svg>
  <p class="web-address">www.harborviewest.com</p>
</section>

<section class="card card-back">
  <div class="back-watermark">Harborview Estates</div>
</section>

</body>
</html>
```